Menu Board and Flyer for a Poke Restaurant

We need for our new Menu board for a Poke restaurant. There will be 2 separate boards. 1 Board for Speciality items, the second for "Build your Own". The menu boards will be installed on a wall.

The first board is going to be 36 W x 48 H inches. The second board will be 72 W x 48 H inches.

I would also like to consolidate the board into a one Page menu flyer that can be printed on an 11 inches x 14 inches Page.

The goal is to have customers focus on the ease of ordering.
We have attached a sample design idea for reference and our logo options. Including the logo is optional.

I have included some sample menus by other companies as attachment and referance.

Files need to include any special fonts used in the design.

Target Market(s)

Young Professionals who love eating healthy, trendy, delicious new food options.

Industry/Entity Type

Fast Food Restaurant

Font styles to use
Serif
Sans Serif

Requirements
Must have
• Simple
• Clean design - NOT busy
• Fun
• Easy to follow
• Highlight a step by step ordering process.
• Light background color
• Files need to include any special fonts used in the design.
Should not have
• script fonts

```html
<!DOCTYPE html>
<html lang="en">
<head>
<meta charset="utf-8">
<title>Build Your Own Poke – Menu Board</title>
<link href="https://fonts.googleapis.com/css2?family=Oswald:wght@300;400;600;700&family=Open+Sans:wght@400;600;700&family=Patrick+Hand&display=swap" rel="stylesheet">
<style>
  :root{
    --ink:#2d2d30;
    --white:#ffffff;
    --sky:#6cc3ea;
    --teal:#5aa5c8;
    --band-light:#b9c2d3;
    --band-dark:#2a2a2c;
    --photo-top:#a9cfe0;
    --photo-bottom:#7fb0c6;
    --text:#2b2b2b;
  }
  *{margin:0;padding:0;box-sizing:border-box}
  html,body{width:1200px;height:777px;overflow:hidden;background:var(--white)}
  .board{position:relative;width:1200px;height:777px;background:var(--white);font-family:"Open Sans",sans-serif;color:var(--text)}
  .hero{position:absolute;left:0;top:0;width:1200px;height:380px;
    background:linear-gradient(90deg,var(--band-light) 45%,#6d7280 62%,var(--band-dark) 80%)}
  .hero-photo{position:absolute;left:0;top:0;width:541px;height:380px;
    background:radial-gradient(ellipse at 60% 55%,#7a3a3a 0 14%,transparent 30%),
               linear-gradient(160deg,#c9a878 0 22%,var(--photo-top) 23%,var(--photo-bottom));}
  .hero-photo::after{content:"";position:absolute;left:25px;top:22px;width:512px;height:335px;border:2px solid rgba(255,255,255,.85)}
  .title{position:absolute;left:262px;top:52px;font-family:"Oswald",sans-serif;font-weight:700;font-size:76px;letter-spacing:-1px;
    color:var(--white);text-shadow:3px 4px 6px rgba(0,0,0,.45);white-space:nowrap;line-height:1;transform:scaleY(1.08)}
  .title .accent{color:var(--sky)}
  .brand{position:absolute;left:955px;top:60px;width:210px;text-align:center;font-family:"Oswald",sans-serif;font-weight:400;
    font-size:30px;line-height:1.1;color:var(--sky);letter-spacing:1px}
  .step-num{position:absolute;width:76px;height:76px;border-radius:50%;background:var(--ink);color:var(--white);
    font-family:"Oswald",sans-serif;font-weight:400;font-size:44px;display:flex;align-items:center;justify-content:center}
  .step-num.on-dark{border:3px solid var(--white)}
  .style-heading{position:absolute;left:575px;top:165px;font-family:"Patrick Hand",sans-serif;font-size:44px;color:var(--white);letter-spacing:1px}
  .style-option{position:absolute;top:222px;color:var(--white);font-family:"Oswald",sans-serif;line-height:1}
  .style-option h3{font-weight:700;font-size:27px;line-height:.98}
  .style-option h3 small{font-size:22px}
  .style-option p{font-weight:300;font-size:20px;line-height:1.4;margin-top:4px}
  .divider{position:absolute;top:232px;width:2px;height:148px;background:var(--white)}
  .step-label{position:absolute;top:409px;font-size:14px;font-weight:700;color:var(--text)}
  .step-title{position:absolute;top:420px;font-family:"Oswald",sans-serif;font-weight:600;font-size:54px;color:var(--teal);letter-spacing:0;line-height:1.2}
  .choices{position:absolute;list-style:none;font-size:22px;line-height:28.3px}
  .choices li{position:relative;padding-left:16px}
  .choices li::before{content:"";position:absolute;left:0;top:12px;width:6px;height:6px;border-radius:50%;background:var(--text)}
  .choices li.cont::before{display:none}
  .bowl-photo{position:absolute;left:893px;top:610px;width:307px;height:167px;
    border-radius:150px 0 0 0;
    background:radial-gradient(circle at 45% 40%,#8b2a2a 0 22%,#3f6b86 40%,#2c4d63 70%,#e9eef0 72%)}
</style>
</head>
<body>
<main class="board">
  <header class="hero">
    <div class="hero-photo" role="img" aria-label="Photo of a poke dish with chili flakes and seaweed on a light blue table"></div>
    <h1 class="title">BUILD YOUR <span class="accent">OWN</span> POKE</h1>
    <div class="brand">Shoreline<br>Poke House</div>

    <div class="step-num on-dark" style="left:486px;top:162px">1.</div>
    <h2 class="style-heading">Choose Your Style</h2>

    <div class="style-option" style="left:582px"><h3>Classic<br>Bowl</h3><p>Regular<br>or Large</p></div>
    <span class="divider" style="left:690px"></span>
    <div class="style-option" style="left:723px"><h3>Surfer<br>Style</h3><p>Poke Served<br>Taco Style</p></div>
    <span class="divider" style="left:849px"></span>
    <div class="style-option" style="left:878px"><h3>Crunchy<br>Bowl</h3><p>One Size,<br>Tostada Style</p></div>
    <span class="divider" style="left:1008px"></span>
    <div class="style-option" style="left:1044px;top:218px"><h3>Just<br>Poke <small>(1lb)</small></h3><p>No Base -<br>1lb of Your<br>Favorite Poke</p></div>
  </header>

  <section class="step">
    <div class="step-num" style="left:29px;top:415px">2.</div>
    <span class="step-label" style="left:118px">CHOOSE YOUR</span>
    <h2 class="step-title" style="left:118px">FISH</h2>
    <ul class="choices" style="left:72px;top:497px">
      <li>Ahi</li><li>Tuna</li><li>Salmon</li><li>Hamachi</li><li>Spicy Tuna</li><li>Shrimp</li><li>Scallop</li>
    </ul>
  </section>

  <section class="step">
    <div class="step-num" style="left:265px;top:412px">3.</div>
    <span class="step-label" style="left:358px">CHOOSE YOUR</span>
    <h2 class="step-title" style="left:358px">TOPPINGS</h2>
    <ul class="choices" style="left:274px;top:496px">
      <li>Crispy Onion</li><li>Green Onion</li><li>Sweet Onion</li><li>Masago</li><li>Cilantro</li><li>Cucumber</li><li>Corn</li><li>Coconut Flakes</li>
    </ul>
    <ul class="choices" style="left:472px;top:496px">
      <li>Hawaiian</li><li class="cont">Sea Salt</li><li>Chili Flakes</li><li>Ogo</li><li>Furikake</li><li>Panko</li><li>Sesame Seed</li><li>Avacado</li>
    </ul>
  </section>

  <section class="step">
    <div class="step-num" style="left:622px;top:414px">4.</div>
    <span class="step-label" style="left:711px">CHOOSE YOUR</span>
    <h2 class="step-title" style="left:711px">SAUCE</h2>
    <ul class="choices" style="left:693px;top:496px">
      <li>Sesame Shoyu</li><li>Sriracha Aioli</li><li>Ponzu</li><li>Sweet Shoyyu</li><li>Wasabi Shoyu</li><li>Sweet Chili</li><li>Chili Lime</li><li>Ginger-Scallion</li><li>Wasabi Creme</li>
    </ul>
  </section>

  <section class="step">
    <div class="step-num" style="left:883px;top:414px">5.</div>
    <span class="step-label" style="left:976px">CHOOSE YOUR</span>
    <h2 class="step-title" style="left:976px">BASE</h2>
    <ul class="choices" style="left:958px;top:494px">
      <li>White Rice</li><li>Brown Rice</li><li>Black Rice</li><li>Mixed Greens</li>
    </ul>
  </section>

  <div class="bowl-photo" role="img" aria-label="Photo of a poke bowl with tuna, rice, avocado and chopsticks"></div>
</main>
</body>
</html>
```